Harborview Estates Business Card for Apartment Buildings

Create business cards for resident managers who run apartment buildings. The audience is the public who are searching for apartment rentals, and current residents who live at the apartment building. Key design element will be incorporating the company logo, however, the logo cannot dominate. The building name and manager name are more important than the logo. Current business card design leaves little room for copy, so we may need to reduce the size on the current card to allow for more space for copy.

Target Market(s)

Adults 18-65 years of age, who are looking for an apartment rental, plus current residents who live at our apartment buildings.

Industry/Entity Type

Property Management

Contact Information for Business Card

A major design element will be use of the company logo. Important property and manager contact information must be part of the design. The size of the logo will need to be reduced to make room for building and manager contact copy.

Font styles to use
Sans Serif

Colors
3176b5
000000
959595
ffffff

Requirements
Must have
• 1) Incorporate the company logo.
• 2) Use the company colors (dark blue, black/grey, over white).
• 3) FEATURE THE BUILDING NAME
• 4) FEATURE THE MANAGER NAME
• 5) The company name is less important than BUILDING and MANAGER
• 6) Manager contact information
• **SEE ATTACHED CREATIVE BRIEF**
Nice to have
• 1) Back of card logo watermark
• 2) Ability to write notes on back of carfd
Should not have
• Avoid letting the company logo dominate the card, the building name and manager are more important than the company logo.

```html
<!DOCTYPE html>
<html lang="en">
<head>
<meta charset="utf-8">
<title>Harborview Estates – Resident Manager Business Card</title>
<link href="https://fonts.googleapis.com/css2?family=Work+Sans:wght@400;500;600&display=swap" rel="stylesheet">
<style>
  :root {
    --brand-blue: #3176b5;
    --card-black: #1b1b1c;
    --mid-grey: #959595;
    --paper-white: #ffffff;
    --backdrop: #3b3532;
  }
  * { box-sizing: border-box; margin: 0; padding: 0; }
  html, body {
    width: 1200px; height: 715px; overflow: hidden;
    background: var(--backdrop);
    font-family: "Work Sans", Arial, sans-serif;
  }
  .canvas { position: relative; width: 1200px; height: 715px; }

  .card {
    position: absolute;
    width: 525px; height: 300px;
    background: var(--card-black);
    border-radius: 4px;
    box-shadow: 0 6px 18px rgba(0,0,0,.45);
    color: var(--paper-white);
  }
  .card--back { left: 45px; top: 110px; border-bottom: 4px solid var(--brand-blue); }
  .card--front { left: 630px; top: 300px; }

  /* back face */
  .brand-lockup {
    position: absolute; left: 0; right: 0; top: 105px;
    display: flex; justify-content: center; align-items: center; gap: 12px;
  }
  .brand-mark { width: 22px; height: 22px; background: var(--brand-blue); }
  .brand-name {
    font-size: 27px; font-weight: 600; letter-spacing: 1px;
    color: var(--paper-white); text-transform: uppercase;
  }
  .back-web {
    position: absolute; left: 0; right: 0; top: 200px;
    text-align: center; font-size: 15px; letter-spacing: 1.5px;
  }
  .back-web .accent { color: var(--brand-blue); }

  /* front face */
  .front-brand {
    position: absolute; left: 30px; top: 0; width: 215px; height: 100%;
    display: flex; flex-direction: column; justify-content: center; align-items: center; gap: 12px;
  }
  .front-brand .brand-mark { width: 46px; height: 46px; }
  .front-brand .brand-name { font-size: 19px; text-align: center; line-height: 1.25; }
  .divider {
    position: absolute; left: 258px; top: 38px; width: 1.5px; height: 224px;
    background: var(--brand-blue);
  }
  .contact { position: absolute; left: 278px; top: 38px; width: 240px; }
  .manager-name {
    font-size: 19px; font-weight: 500; color: var(--brand-blue);
    text-transform: uppercase; letter-spacing: .5px;
  }
  .manager-title { font-size: 13.5px; margin-top: 3px; }
  .building-name {
    font-size: 13px; font-weight: 600; color: var(--brand-blue);
    text-transform: uppercase; margin-top: 10px; letter-spacing: .3px;
  }
  .address { font-size: 13.5px; line-height: 1.3; }
  .contact-list { list-style: none; margin-top: 8px; }
  .contact-list li {
    display: flex; align-items: center; gap: 9px;
    font-size: 13.5px; line-height: 1.45;
  }
  .contact-list svg { width: 11px; height: 11px; flex: none; fill: var(--brand-blue); }
  .contact-list .accent { color: var(--brand-blue); }
</style>
</head>
<body>
<main class="canvas">

  <section class="card card--back" aria-label="Card back">
    <div class="brand-lockup">
      <span class="brand-mark"></span>
      <span class="brand-name">Harborview Estates LLC</span>
    </div>
    <p class="back-web">www.<span class="accent">harborviewest</span>.com</p>
  </section>

  <section class="card card--front" aria-label="Card front">
    <div class="front-brand">
      <span class="brand-mark"></span>
      <span class="brand-name">Harborview<br>Estates</span>
    </div>
    <div class="divider"></div>
    <div class="contact">
      <h1 class="manager-name">Marisol Quintero</h1>
      <p class="manager-title">Resident Manager</p>
      <h2 class="building-name">Cedar Crest Apartments</h2>
      <p class="address">1482 Juniper Avenue<br>Bayport, CA 92180</p>
      <ul class="contact-list">
        <li><svg viewBox="0 0 24 24"><path d="M6.6 10.8a15 15 0 0 0 6.6 6.6l2.2-2.2c.3-.3.7-.4 1-.2 1.1.4 2.3.6 3.6.6.6 0 1 .4 1 1V20c0 .6-.4 1-1 1A17 17 0 0 1 3 4c0-.6.4-1 1-1h3.5c.6 0 1 .4 1 1 0 1.3.2 2.5.6 3.6.1.3 0 .7-.2 1z"/></svg>555-014-2281</li>
        <li><svg viewBox="0 0 24 24"><rect x="2" y="8" width="20" height="10" rx="2"/><rect x="6" y="3" width="12" height="6"/><rect x="6" y="15" width="12" height="6"/></svg>555-017-6034</li>
        <li><svg viewBox="0 0 24 24"><path d="M7 1h10a2 2 0 0 1 2 2v18a2 2 0 0 1-2 2H7a2 2 0 0 1-2-2V3a2 2 0 0 1 2-2zm0 3v15h10V4z"/></svg>555-019-4417</li>
        <li><svg viewBox="0 0 24 24"><path d="M2 5h20v14H2zm2 2v.5l8 5 8-5V7z"/></svg>marisol@harborviewest.com</li>
        <li><svg viewBox="0 0 24 24"><path d="M12 2a10 10 0 1 0 0 20 10 10 0 0 0 0-20zm1 2.1c1.3 1.5 2.1 3.6 2.3 5.9H13zm-2 0V10H8.7c.2-2.3 1-4.4 2.3-5.9zM4.1 12h4.6c.1 2.4.9 4.6 2.3 6.2A8 8 0 0 1 4.1 12zm8.9 6.2c1.4-1.6 2.2-3.8 2.3-6.2h4.6a8 8 0 0 1-6.9 6.2z"/></svg>www.<span class="accent">harborviewest</span>.com</li>
      </ul>
    </div>
  </section>

</main>
</body>
</html>
```